Therapy Services & Training

I provide counseling/therapy to individuals and families. I also travel the country and provide training at conferences.
I would like to see a card which takes my company name and design a logo using the letters "HCAL".
Target Market(s)
Therapists, non-profit organizations, clients looking for therapy
Industry/Entity Type
Training
Contact Information for Business Card
Harborstone Clinical Advising & Learning LLC
Dana Pellham, M.S.W., LCSW
Clinical Therapist & Trainer
Providing clinical therapy services to individuals, families, couples & children. We also provide life coaching and crisis training.
counselordana@mailbrook.example
www.harborstoneclinicaladvising.example
(555) 214-3097
Cedarbend, IL 60100
(BACK SIDE OF CARD)
We are certified by the Baseline Ongoing Bar Studies (BOBS) Panel of the Prairie State High Tribunal to provide Continuing Legal Education (CLE) credits to Illinois attorneys. Call about what courses we offer! (555) 214-3097

```html
<!DOCTYPE html>
<html lang="en">
<head>
<meta charset="utf-8">
<title>Harborstone Clinical Advising &amp; Learning LLC — Business Card</title>
<link rel="stylesheet" href="https://fonts.googleapis.com/css2?family=Nunito+Sans:wght@300;400;600;700&display=swap">
<style>
  :root {
    --paper: #ffffff;
    --ink: #111111;
    --violet: #3b1ff0;
    --sky: #3a86f0;
    --sky-soft: #6f93e6;
    --mark-dot: #3f8df8;
  }
  html, body {
    margin: 0;
    padding: 0;
    overflow: hidden;
    background: var(--paper);
  }
  .card {
    position: relative;
    width: 1200px;
    height: 702px;
    background: var(--paper);
    font-family: "Nunito Sans", "Helvetica Neue", Arial, sans-serif;
    overflow: hidden;
  }
  .company {
    position: absolute;
    left: 83px;
    top: 68px;
    margin: 0;
    font-size: 45px;
    line-height: 60px;
    font-weight: 400;
    color: var(--ink);
  }
  .brand-mark {
    position: absolute;
    left: 880px;
    width: 236px;
    top: 92px;
    height: 252px;
    display: flex;
    flex-direction: column;
    align-items: center;
    justify-content: center;
    gap: 14px;
  }
  .brand-mark__dot {
    width: 96px;
    height: 96px;
    border-radius: 50%;
    background: var(--mark-dot);
  }
  .brand-mark__name {
    font-size: 78px;
    font-weight: 700;
    color: var(--violet);
    letter-spacing: 3px;
    line-height: 1;
  }
  .person {
    position: absolute;
    left: 83px;
    top: 300px;
    margin: 0;
    white-space: nowrap;
  }
  .person__name {
    font-size: 70px;
    font-weight: 700;
    color: var(--violet);
    letter-spacing: -0.5px;
  }
  .person__credentials {
    font-size: 40px;
    font-weight: 400;
    color: var(--ink);
    margin-left: 8px;
  }
  .role {
    position: absolute;
    left: 83px;
    top: 410px;
    margin: 0;
    font-size: 31px;
    font-weight: 600;
    color: var(--ink);
  }
  .contact {
    position: absolute;
    left: 81px;
    top: 456px;
    margin: 0;
    padding: 0;
    list-style: none;
    font-size: 30px;
    line-height: 44px;
    font-weight: 400;
    color: var(--sky);
  }
  .contact__web {
    letter-spacing: -0.6px;
  }
  .services {
    position: absolute;
    right: 84px;
    top: 456px;
    margin: 0;
    text-align: right;
    font-size: 31px;
    line-height: 44px;
    font-weight: 300;
    color: var(--sky-soft);
  }
</style>
</head>
<body>
  <main class="card">
    <h1 class="company">Harborstone Clinical<br>Advising &amp; Learning LLC</h1>

    <div class="brand-mark">
      <span class="brand-mark__dot"></span>
      <span class="brand-mark__name">HCAL</span>
    </div>

    <p class="person">
      <span class="person__name">Dana Pellham</span><span class="person__credentials">M.S.W., LCSW</span>
    </p>

    <p class="role">Clinical Therapist &amp; Trainer</p>

    <ul class="contact">
      <li class="contact__email">counselordana@mailbrook.example</li>
      <li class="contact__web">www.harborstoneclinicaladvising.example</li>
      <li class="contact__phone">(555) 214-3097</li>
      <li class="contact__location">Cedarbend, IL 60100</li>
    </ul>

    <p class="services">
      Providing clinical therapy services<br>
      to individuals, families, couples,<br>
      and children. We also provide<br>
      life coaching and crisis training.
    </p>
  </main>
</body>
</html>
```